Modern, clean and professional Wordpress design for a safety training company!

We are currently in the process of creating a new website for our business. We have hired a website developer and the main structure of our new Wordpress site is complete. We now need an overall design plan for the site. We need a very clean, professional and easy to follow website. Most of our website visitors only spend about 30-45 secs on our sites "shopping " so it is imperative that we have a strong Home Page.
Our company specializes in CPR and First Aid Certification Classes to businesses and individuals throughout Northern California. We provide these certifications two ways: ONSITE-We come to you, and HOSTED-we offer weekly classes at our 2 locations.
Our design needs to use the general green and blue colors of our logo. But we also like white.
The final design MUST communicate a legitimate, trustworthy and professional business. Our industry is VERY competitive and we need to STAND OUT.
Currently, the NEW website that we need a new design for is www.LifelineDrillWorks.com
Our old website is www.RescuePrepValleyHub.com and we really do like the design of this website, but we just needed a Wordpress site for SEO purposes.
These are 3 websites that we really:
http://morvaliontech.com/
http://www.tralbex.com/
https://www.plivant.com/
I have attached our Logo and other images if you need to use them but looking at the current two sites will be you best help.
Target Market(s)
1) Large businesses and industries that are looking for a company to provide ONSITE safety training classes at their office or place of work.
2) Individuals that need certifications for their jobs and other needs. These individuals are looking for a legitimate, trustworthy and professional environment to complete their training class.

```html
<!DOCTYPE html>
<html lang="en">
<head>
<meta charset="utf-8">
<title>Keystone Response Academy</title>
<link rel="stylesheet" href="https://fonts.googleapis.com/css2?family=Open+Sans:ital,wght@0,400;0,600;0,700;1,700&display=swap">
<style>
:root{
  --green:#7a9a14;
  --green-dark:#6b8810;
  --navy:#12337a;
  --blue:#1f4aa0;
  --ink:#444;
  --gray-panel:#e1e1e1;
  --white:#fff;
}
*{box-sizing:border-box;margin:0;padding:0}
html,body{width:954px;height:1200px;overflow:hidden;background:var(--white)}
body{font-family:"Open Sans",Arial,sans-serif;color:var(--ink);position:relative}
.abs{position:absolute}
.top-rule{left:0;top:0;width:954px;height:3px;background:var(--green)}
.brand{left:78px;top:34px;display:flex;align-items:center;gap:6px;color:var(--navy);font-weight:700;font-size:15px;line-height:1.1}
.brand-dot{width:12px;height:12px;border-radius:50%;background:var(--green)}
.nav{left:290px;top:80px;display:flex;gap:0;font-size:9.6px;font-weight:600;color:var(--navy)}
.nav a{color:inherit;text-decoration:none;padding:4px 0;height:19px;line-height:11px;margin-right:22px;white-space:nowrap}
.nav a.active{background:var(--green);color:var(--white);padding:4px 15px;margin-right:9px}
.search{left:843px;top:81px}
.hero{left:0;top:104px;width:954px;height:418px;background:linear-gradient(160deg,#c9ccd0 0%,#8a8c94 35%,#4a4d5a 70%,#2e3140 100%)}
.hero-box{left:210px;top:220px;width:534px;height:171px;background:rgba(230,232,236,.82);text-align:center}
.hero-title{margin-top:26px;font-size:20px;font-style:italic;font-weight:700;color:var(--navy)}
.hero-sub{margin-top:8px;font-size:12.4px;font-weight:600;color:#222}
.hero-text{margin:6px auto 0;width:490px;font-size:8.6px;line-height:16px;color:var(--navy)}
.btn-green{display:inline-block;background:var(--green);color:var(--white);font-size:9.5px;font-weight:600;text-align:center}
.hero-btn{margin-top:12px;width:122px;height:25px;line-height:25px}
.dots{left:720px;top:490px;display:flex;gap:5px}
.dots span{width:16px;height:16px;border-radius:50%;border:2px solid var(--white);background:var(--navy)}
.dots span.on{background:transparent}
.welcome{left:0;top:538px;width:954px;text-align:center}
.welcome h1{font-size:20px;font-weight:400;color:var(--navy)}
.welcome-line{top:552px;width:128px;height:1px;background:var(--navy)}
.welcome p{margin:10px auto 0;width:700px;font-size:9.6px;line-height:17px}
.welcome .btn-green{margin-top:14px;width:110px;height:25px;line-height:25px}
.services{left:78px;top:665px;width:798px;height:240px;background:var(--gray-panel);display:flex;justify-content:space-between;padding:19px 42px 0 45px}
.card{width:190px;text-align:center}
.card-photo{margin:0 auto;width:179px;height:116px;border:1px solid #888;border-radius:2px}
.card h3{margin-top:10px;font-size:8.8px;font-weight:700;color:var(--navy)}
.card p{margin-top:3px;font-size:8.4px;line-height:16px;height:32px}
.btn-navy{display:inline-block;margin-top:6px;background:var(--navy);color:var(--white);font-size:9px;height:23px;line-height:23px;padding:0 9px;border-radius:2px}
.news{left:78px;top:935px;width:262px}
.news h2{font-size:12.8px;font-weight:600;color:#222}
.news h4{margin-top:5px;font-size:8.6px;font-weight:600;color:var(--blue)}
.news p{margin-top:6px;font-size:8.4px;line-height:16px}
.news .more{color:var(--navy);font-weight:700}
.price{float:right;color:var(--navy);font-weight:600;font-size:9px}
.price u{margin-left:3px}
.news .item2{margin-top:9px}
.map{left:385px;top:970px;width:208px;height:125px;background:#e8e4dc}
.map-label{left:391px;top:971px;width:122px;height:34px;background:var(--white);font-size:7.5px;padding:4px 6px;color:#222;font-weight:700;box-shadow:0 1px 2px rgba(0,0,0,.2)}
.map-label span{display:block;font-weight:400;color:var(--blue);font-size:6.5px;margin-top:2px}
.office-link{left:385px;top:1109px;width:208px;text-align:center;font-size:9.6px;font-weight:600;color:var(--navy);text-decoration:underline}
.contact{left:698px;top:978px;font-size:9.5px;line-height:16.5px}
.contact h2{font-size:12.8px;font-weight:600;color:#222;margin-bottom:4px}
.social{left:698px;top:1093px;display:flex;gap:7px}
.social span{width:22px;height:22px;border-radius:3px;background:var(--blue)}
.badge{left:806px;top:1055px;width:40px;height:62px;border:2px solid var(--navy);border-radius:3px;background:#eef1f7}
.footer{left:0;top:1151px;width:954px;height:49px;background:var(--green);color:var(--white);font-size:9.6px}
.footer-nav{position:absolute;left:78px;top:17px;display:flex;gap:14px}
.copyright{position:absolute;right:78px;top:17px}
</style>
</head>
<body>
<div class="abs top-rule"></div>

<header>
  <div class="abs brand"><span class="brand-dot"></span><span>Keystone Response<br>Academy</span></div>
  <nav class="abs nav">
    <a class="active">HOME</a><a>CLASS CALENDER</a><a>CLASSES FOR GROUPS</a><a>CERTIFICATION CLASSES</a><a>ABOUT US</a><a>POLICIES</a>
  </nav>
  <svg class="abs search" width="18" height="16" viewBox="0 0 18 16" aria-label="Search"><circle cx="6.5" cy="6.5" r="4.8" fill="none" stroke="#12337a" stroke-width="2"/><line x1="10" y1="10" x2="16" y2="14.5" stroke="#12337a" stroke-width="3" stroke-linecap="round"/></svg>
</header>

<section>
  <div class="abs hero" role="img" aria-label="Photo of a classroom of students attending a training session"></div>
  <div class="abs hero-box">
    <h1 class="hero-title">KEYSTONE RESPONSE ACADEMY!</h1>
    <h2 class="hero-sub">CPR AND FIRST AID CERTIFICATION CLASSES</h2>
    <p class="hero-text">Taught by experienced Firefighters, our classes are much shorter and provide common sense knowledge and skills to each student to help prepare them for actual emergencies.</p>
    <span class="btn-green hero-btn">LEARN MORE</span>
  </div>
  <div class="abs dots"><span></span><span></span><span></span><span class="on"></span></div>
</section>

<section>
  <div class="abs welcome-line" style="left:217px"></div>
  <div class="abs welcome-line" style="left:612px"></div>
  <div class="abs welcome">
    <h1>WELCOME TO KRA !</h1>
    <p>Keystone Response Academy is Northern California's leader in CPR, BLS, and Basic First Aid Certifications! Taught by experienced Firefighters, our classes are much shorter and provide common sense knowledge and skills to each student to help prepare them for actual emergencies.</p>
    <span class="btn-green">READ MORE</span>
  </div>
</section>

<section class="abs services">
  <article class="card">
    <div class="card-photo" role="img" aria-label="Photo of hands performing CPR training" style="background:linear-gradient(135deg,#5a5f6e,#2a2c36)"></div>
    <h3>CPR TRAINING</h3>
    <p>Our company specializes in CPR and First Aid Certification Classes to businesses ....</p>
    <span class="btn-navy">READ MORE</span>
  </article>
  <article class="card">
    <div class="card-photo" role="img" aria-label="Photo of medical staff in a BLS session" style="background:linear-gradient(135deg,#c9b79e,#6d6fa8)"></div>
    <h3>BLS TRAINING</h3>
    <p>We provide these certifications two ways: ONSITE-We come to you,......</p>
    <span class="btn-navy">READ MORE</span>
  </article>
  <article class="card">
    <div class="card-photo" role="img" aria-label="Photo of infant training manikins on a table" style="background:linear-gradient(135deg,#d8d8d8,#c99f8a)"></div>
    <h3>BASIC FIRST AID</h3>
    <p>certifications two ways: ONSITE-We come to you, and HOSTED-we offer weekly classes</p>
    <span class="btn-navy">READ MORE</span>
  </article>
</section>

<section class="abs news">
  <h2>LATEST NEWS</h2>
  <h4>ADULT/CHILD/INFANT</h4>
  <p>Gravida atcur ecuus istique orci ac sis ultricpharetra gna. Donec alsuada orcnc sit ameteros. Loremipsum dolor sit at consc tetuer aiing elituris fermentum tumagna. Sed aoreet aliquam leo. Ut te dt elentu vel leife. <span class="more">[...]</span><span class="price">$39<u>REGISTERNOW</u></span></p>
  <h4 class="item2">HEALTHCARE/DENTAL</h4>
  <p>Gravida atcur ecuus istique orci ac sis ultricpharetra gna. Donec alsuada orcnc sit ameteros. Loremipsum dolor sit at consc tetuer aiing elituris fermentum tumagna. Sedaoreet aliquam leo. Ut te dt elentu vel leife. <span class="more">[...]</span><span class="price">$49<u>REGISTERNOW</u></span></p>
</section>

<div class="abs map" role="img" aria-label="Street map showing the office location"></div>
<div class="abs map-label">4820 Alder Bend Rd #118<span>Map view</span></div>
<div class="abs office-link">CLICK TO VIEW OUR OFFICE</div>

<section class="abs contact">
  <h2>CONTACT</h2>
  1234 ,Building Number,<br>Street number,<br>City, ABCD<br>1800 000 000<br>1800 000 002
</section>
<div class="abs social" aria-label="Social links"><span></span><span></span><span></span></div>
<div class="abs badge" aria-label="Accreditation badge"></div>

<footer class="abs footer">
  <div class="footer-nav"><span>Home</span><span>Class</span><span>Calender</span><span>Certification Classes</span><span>Classes for Groups</span><span>About Us</span><span>Policies</span></div>
  <div class="copyright">Copyright © 2015 Keystone Response Academy. All rights reserved.</div>
</footer>
</body>
</html>
```